Wedding Ceremony Equipment Hire Business Card

I need a business card design for a new business I created called Vowline Rentals. We hire out Wedding Ceremony equipment and decorations mainly for beach and garden wedding ceremonies that include delivery, set up and dismantle. We do offer DIY Chair Hire as well.
I'd like to have a similar design and colours to our website:
www.vowlinerentals.com.au
If possible would like the front to incorporate our information and logo and the back to have two faded example pictures of our wedding ceremonies.
I have attached two photos and our logo. Please let me know if you need a better pic of our logo though.

Target Market(s)

Newly engaged couples, aged 25 and upwards

Industry/Entity Type

Wedding

Contact Information for Business Card

Vowline Rentals
Mira Holt
0412 908 146
hello@vowlinerentals.com.au
www.vowlinesocial.com/VowlineRentals

```html
<!DOCTYPE html>
<html lang="en">
<head>
<meta charset="utf-8">
<title>Vowline Rentals – Business Card</title>
<link href="https://fonts.googleapis.com/css2?family=EB+Garamond:ital,wght@1,400;1,500&display=swap" rel="stylesheet">
<style>
  :root {
    --paper: #ffffff;
    --charcoal: #1a1f20;
    --mint: #8ef5a0;
    --mint-soft: #b9f9c4;
    --mint-line: #d8fde0;
  }
  html, body {
    margin: 0;
    padding: 0;
    width: 1200px;
    height: 741px;
    overflow: hidden;
    background: var(--paper);
  }
  .card {
    position: absolute;
    left: 46px;
    top: 46px;
    width: 1106px;
    height: 647px;
    background: var(--charcoal);
    font-family: "EB Garamond", Georgia, serif;
    font-style: italic;
  }
  .brand-band {
    position: absolute;
    left: 0;
    top: 228px;
    width: 100%;
    height: 193px;
    background: var(--mint);
  }
  .band-ornament {
    position: absolute;
    inset: 0;
    background:
      radial-gradient(ellipse 180px 90px at 78% 30%, var(--mint-soft), transparent 70%),
      radial-gradient(ellipse 160px 80px at 22% 60%, var(--mint-soft), transparent 70%),
      var(--mint);
  }
  .brand-name {
    position: absolute;
    left: 0;
    right: 0;
    top: 50%;
    transform: translateY(-50%);
    margin: 0;
    text-align: center;
    font-size: 76px;
    font-weight: 500;
    color: var(--charcoal);
    line-height: 1;
  }
  .contact {
    position: absolute;
    left: 0;
    right: 0;
    top: 448px;
    text-align: center;
    color: var(--mint);
  }
  .contact-name {
    margin: 0;
    font-size: 40px;
    font-weight: 400;
    line-height: 1;
  }
  .contact-rule {
    width: 361px;
    height: 3px;
    margin: 18px auto 12px;
    background: var(--mint-line);
    border: 0;
  }
  .contact-list {
    list-style: none;
    margin: 0;
    padding: 0;
    font-size: 18px;
    line-height: 25px;
  }
  .contact-list .phone {
    font-size: 21px;
  }
</style>
</head>
<body>
  <main class="card">
    <section class="brand-band">
      <div class="band-ornament" role="img" aria-label="Soft pale green swirling vine and leaf ornament across the band"></div>
      <h1 class="brand-name">Vowline Rentals</h1>
    </section>
    <section class="contact">
      <h2 class="contact-name">Mira Holt</h2>
      <hr class="contact-rule">
      <ul class="contact-list">
        <li class="phone">Call us: 0412 908 146</li>
        <li>hello@vowlinerentals.com.au</li>
        <li>www.vowlinerentals.com.au</li>
        <li>www.vowlinesocial.com/VowlineRentals</li>
      </ul>
    </section>
  </main>
</body>
</html>
```